Heron Dusk business card design

I make handmade colourful women's beaded jewellery (necklaces and earnings).
I require a business card to be designed to truly reflect my jewellery, that is, it is different and stands out.
I would like the business card to look creative, arty, gentle and feminine and fit in with the look of my website and logo (already developed).
I would like the business card to have strong use of the water reeds that are flowing in the wind (please see the banner image on my website www.herondusk.net and attached files).

Target Market(s)

Women who are fashion conscious, hip and funky. My audience like things that are a little different and stand out in a crowd.These women are aged in their 20's-40's.

Industry/Entity Type

Jewelry

Contact Information for Business Card

Please include the following items:
1) my logo: Heron Dusk
2) my name, address and phone number: Darla Fontenot, Sydney, Australia, 0498 315 270
3) my web details: www.herondusk.net, info@herondusk.net, www.facebook.com/herondusk

Font styles to use
Other font styles liked:
• Remachine Script

Requirements
Must have
• My business card must have the following:
• 1) my personal details including all my website contacts (see above).
• 2) Heron Dusk logo
• 3) Reeds flowing in the wind (see my banner image on my website www.herondusk.net or see attached files).
Nice to have
• A sunrise in the background (rising over water)
• I would prefer that the colour scheme to fit with the Heron Dusk logo, that is the colours of an early morning sunrise i.e yellows, oranges. The use of black and white is fine.
Should not have
• I do not like a commercial manufactured look with hard edges. I would like a look that is soft and reflects an artistic, creative and independent business.

```html
<!DOCTYPE html>
<html lang="en">
<head>
<meta charset="utf-8">
<title>Heron Dusk — Business Card</title>
<link rel="stylesheet" href="https://fonts.googleapis.com/css2?family=Mulish:wght@400;500&display=swap">
<style>
  :root {
    --backdrop: #3b3b3b;
    --card-white: #ffffff;
    --sun-yellow: #ffe600;
    --sun-gold: #ffc20e;
    --dusk-orange: #f7941d;
    --deep-orange: #f26f21;
    --ink: #231f20;
    --ink-soft: rgba(35, 31, 32, 0.18);
    --ink-mid: rgba(35, 31, 32, 0.62);
    --rule-grey: #9a9a9a;
    --radius: 19px;
  }
  * { margin: 0; padding: 0; box-sizing: border-box; }
  html, body {
    width: 1105px;
    height: 1200px;
    overflow: hidden;
    background: var(--backdrop);
    font-family: "Mulish", "Helvetica Neue", Arial, sans-serif;
    color: var(--ink);
  }
  .canvas { position: relative; width: 1105px; height: 1200px; }

  .card {
    position: absolute;
    left: 196px;
    width: 720px;
    height: 412px;
    border-radius: var(--radius);
    overflow: hidden;
  }

  /* Front */
  .card--front { top: 146px; }
  .front-scene {
    position: absolute; inset: 0;
    background:
      radial-gradient(circle at 71% 31%, var(--sun-yellow) 0 17%, rgba(255,230,0,0.35) 24%, rgba(255,230,0,0) 42%),
      linear-gradient(180deg, var(--sun-gold) 0%, #ffb612 62%, var(--dusk-orange) 70%, #fbb03b 82%, var(--sun-gold) 100%);
  }
  .front-reeds {
    position: absolute;
    left: 418px;
    top: 88px;
    width: 270px;
    height: 324px;
    border-radius: 120px 120px 0 0;
    background: linear-gradient(180deg, var(--ink-soft) 0%, var(--ink-mid) 100%);
  }
  .front-identity {
    position: absolute;
    left: 101px;
    top: 278px;
    width: 300px;
    text-align: center;
  }
  .front-identity__name {
    font-size: 33px;
    font-weight: 400;
    line-height: 1.1;
    white-space: nowrap;
  }
  .front-identity__role {
    font-size: 22px;
    font-weight: 400;
    margin-top: 6px;
  }

  /* Back */
  .card--back { top: 602px; background: var(--card-white); }
  .brand {
    position: absolute;
    top: 112px;
    left: 0; right: 0;
    display: flex;
    align-items: center;
    justify-content: center;
    gap: 18px;
  }
  .brand__dot {
    width: 90px; height: 90px;
    border-radius: 50%;
    background: var(--dusk-orange);
  }
  .brand__name {
    font-size: 44px;
    font-weight: 500;
    color: var(--ink);
  }
  .contact {
    position: absolute;
    left: 0; right: 0;
    text-align: center;
    font-size: 20px;
    font-weight: 400;
  }
  .contact--address { top: 273px; }
  .contact--lines { top: 301px; }
  .social {
    position: absolute;
    top: 340px;
    left: 0; right: 0;
    display: flex;
    align-items: center;
    justify-content: center;
    gap: 8px;
  }
  .social__rule { width: 72px; height: 1px; background: var(--rule-grey); }
  .social__rule--left { margin-right: 6px; }
  .social__rule--right { margin-left: 6px; }
  .social__dot {
    width: 26px; height: 26px;
    border-radius: 50%;
    background: var(--ink);
  }
  .colour-bar {
    position: absolute;
    left: 0; right: 0; bottom: 0;
    height: 15px;
    display: flex;
    gap: 3px;
  }
  .colour-bar__orange { width: 497px; background: var(--dusk-orange); }
  .colour-bar__yellow { width: 112px; background: var(--sun-gold); }
  .colour-bar__black { flex: 1; background: var(--ink); }
</style>
</head>
<body>
<main class="canvas">
  <section class="card card--front">
    <div class="front-scene" role="img" aria-label="Rising sun over water with radiating sun rays"></div>
    <div class="front-reeds" role="img" aria-label="Silhouette of a heron standing on a post with water reeds flowing in the wind"></div>
    <div class="front-identity">
      <p class="front-identity__name">WREN CALLOWAY</p>
      <p class="front-identity__role">CEO/Founder</p>
    </div>
  </section>

  <section class="card card--back">
    <div class="brand">
      <span class="brand__dot"></span>
      <span class="brand__name">Heron Dusk</span>
    </div>
    <p class="contact contact--address">Darla Fontenot, Sydney, Australia</p>
    <p class="contact contact--lines">0498 315 270 | info@herondusk.net | herondusk.net</p>
    <div class="social" aria-label="Social links">
      <span class="social__rule social__rule--left"></span>
      <span class="social__dot"></span>
      <span class="social__dot"></span>
      <span class="social__dot"></span>
      <span class="social__dot"></span>
      <span class="social__rule social__rule--right"></span>
    </div>
    <div class="colour-bar">
      <span class="colour-bar__orange"></span>
      <span class="colour-bar__yellow"></span>
      <span class="colour-bar__black"></span>
    </div>
  </section>
</main>
</body>
</html>
```